Redesign Of Current Landing Page

I need to redesign this landing page https://www.brightlanepromo.biz/?page=landing&landing=23 (Please do not opt in because when you do it will show you the home page. Please clear your cookies before going to this url above to view the 1 page landing page.)

Please use my updated website as a reference for colors and logo.
http://sitecradlewerk.com/dh/bpq/index.html

I would like the call to action to be a button that opens into a lead form...

Button would be "Download Samples"

Target Market(s)

small business owners

Industry/Entity Type

Marketing

Number of Pages Required

1 page

Colors

Designer to choose colors to be used in the design.

Requirements
Must have
• must be full responsive on all devices
Nice to have
• must have a legitimate professional apeal to it
Should not have
• open

```html
<!DOCTYPE html>
<html lang="en">
<head>
<meta charset="utf-8">
<title>Bright Lane Promo Group – Landing</title>
<link rel="stylesheet" href="https://fonts.googleapis.com/css2?family=Roboto:wght@400;500;700&display=swap">
<style>
:root{
  --blue:#0b6dbd;
  --blue-dark:#0a4f8a;
  --grey-btn:#9b9b9b;
  --page:#f3f3f3;
  --ink:#333;
  --muted:#666;
  --footer:#7d7d7d;
}
*{margin:0;padding:0;box-sizing:border-box}
html,body{width:914px;height:1200px;overflow:hidden}
body{font-family:'Roboto',sans-serif;background:var(--page);color:var(--ink);position:relative}
.abs{position:absolute}
.header{left:0;top:0;width:914px;height:68px;background:#f7f7f7}
.brand{left:90px;top:20px;display:flex;align-items:center;gap:7px}
.brand-dot{width:26px;height:26px;border-radius:50%;background:var(--blue-dark)}
.brand-name{font-size:24px;font-weight:700;color:#222;letter-spacing:1px}
.call-icon{left:500px;top:14px;width:30px;height:30px;border-radius:50%;background:var(--blue);display:flex;align-items:center;justify-content:center}
.call-label{left:542px;top:12px;font-size:10px;color:var(--muted)}
.call-number{left:540px;top:24px;font-size:18px;font-weight:700;color:var(--blue);letter-spacing:.5px}
.call-hours{left:542px;top:49px;font-size:9px;color:var(--muted)}
.btn{background:var(--grey-btn);color:#fff;font-weight:700;border-radius:4px;display:flex;align-items:center;justify-content:center}
.header-btn{left:688px;top:19px;width:150px;height:33px;font-size:14px}
.hero{left:0;top:68px;width:914px;height:382px;background:linear-gradient(90deg,var(--blue-dark) 0%,var(--blue-dark) 38%,#5f86a8 60%,#d8d2cb 100%)}
.hero-title{left:101px;top:172px;font-size:27px;font-weight:700;color:#fff}
.hero-sub{left:101px;top:206px;font-size:20px;color:#fff;line-height:24px;width:320px}
.hero-note{left:102px;top:256px;font-size:11px;color:#fff;line-height:16px}
.hero-btn{left:100px;top:298px;width:190px;height:32px;font-size:14px;justify-content:flex-start;padding-left:21px}
.hero-arrow{top:358px;width:30px;height:30px;border-radius:50%;background:#083b66;display:flex;align-items:center;justify-content:center}
.intro{left:75px;top:506px;width:763px;height:174px;background:var(--blue);color:#fff;text-align:center;font-size:9.6px;line-height:11px}
.intro p{position:absolute;left:40px;width:683px}
.intro-tab{left:317px;top:500px;width:99px;height:8px;background:var(--blue-dark)}
.wide-btn{width:314px;height:32px;font-size:14px;left:300px}
.section-title{left:0;width:914px;text-align:center;font-size:16px;font-weight:700;color:var(--blue-dark)}
.benefit{top:750px;width:120px;text-align:center;font-size:8.5px;line-height:11.5px;color:var(--ink)}
.benefit svg{display:block;margin:0 auto 20px}
.quote-badge{left:437px;top:956px;width:40px;height:40px;border-radius:50%;background:#555;display:flex;align-items:center;justify-content:center;color:#fff;font-size:26px;font-weight:700}
.quote-text{left:148px;top:1006px;width:618px;text-align:center;font-size:9.6px;line-height:19.6px;color:var(--ink)}
.quote-name{left:0;top:1101px;width:914px;text-align:center;font-size:12px;font-weight:500;color:var(--blue-dark)}
.quote-place{left:0;top:1120px;width:914px;text-align:center;font-size:12px;font-weight:500;color:var(--muted)}
.footer{left:0;top:1158px;width:914px;height:42px;background:var(--footer);color:#fff;font-size:10px;display:flex;align-items:center;justify-content:center}
.footer-mark{left:860px;top:1175px;font-size:9px;font-weight:700;color:#fff}
.overlay{left:0;top:0;width:914px;height:1200px;background:rgba(0,0,0,.55)}
.modal{left:232px;top:248px;width:422px;height:254px;background:#fff;border-radius:5px;overflow:hidden}
.modal-photo{left:0;top:0;width:201px;height:254px;background:linear-gradient(160deg,#e6ece9 0%,#9fb0b4 45%,#4d5d6b 100%)}
.close{left:382px;top:4px;font-size:9.5px;color:#444;display:flex;align-items:center;gap:4px}
.close span{width:15px;height:15px;border-radius:50%;background:#999;color:#fff;font-size:9px;font-weight:700;display:flex;align-items:center;justify-content:center}
.form-title{left:201px;top:26px;width:221px;text-align:center;font-size:16px;font-weight:700;color:var(--blue)}
.form-note{left:201px;top:47px;width:221px;text-align:center;font-size:7.5px;line-height:12px;color:var(--muted)}
.field{left:230px;width:162px;height:23px;border:1px solid #cfcfcf;border-radius:2px;font-size:8px;color:#222;padding-left:10px;display:flex;align-items:center}
.form-btn{left:230px;top:190px;width:158px;height:26px;font-size:11.5px}
</style>
</head>
<body>
<header class="abs header">
  <div class="abs brand"><div class="brand-dot"></div><div class="brand-name">BLPG</div></div>
  <div class="abs call-icon"><svg width="14" height="14" viewBox="0 0 24 24"><path fill="#fff" d="M6.6 10.8a15 15 0 0 0 6.6 6.6l2.2-2.2c.3-.3.7-.4 1-.2 1.1.4 2.3.6 3.6.6.6 0 1 .4 1 1V20c0 .6-.4 1-1 1A17 17 0 0 1 3 4c0-.6.4-1 1-1h3.5c.6 0 1 .4 1 1 0 1.3.2 2.5.6 3.6.1.3 0 .7-.2 1z"/></svg></div>
  <div class="abs call-label">Call Us</div>
  <div class="abs call-number">1-800-555-0147</div>
  <div class="abs call-hours">Mon-Fri 8am-5pm PST</div>
  <div class="abs btn header-btn">Email Us Samples</div>
</header>

<section class="abs hero" role="img" aria-label="Photo of a team of young professionals working together at a desk"></section>
<h1 class="abs hero-title">Attract more customers</h1>
<p class="abs hero-sub">who spend more money with your business more often!</p>
<p class="abs hero-note">Using Free Vacation &amp; Cruise Incentives<br>Without Breaking The Bank!</p>
<div class="abs btn hero-btn">Download Free Samples</div>
<div class="abs hero-arrow" style="left:103px"><svg width="10" height="12" viewBox="0 0 10 12"><path d="M7 1 2 6l5 5" stroke="#fff" stroke-width="1.8" fill="none"/></svg></div>
<div class="abs hero-arrow" style="left:143px"><svg width="10" height="12" viewBox="0 0 10 12"><path d="m3 1 5 5-5 5" stroke="#fff" stroke-width="1.8" fill="none"/></svg></div>

<div class="abs intro-tab"></div>
<section class="abs intro">
  <p style="top:22px">Being able to create exciting give away promotions that will boost your sales without ever having to worry about cost.</p>
  <p style="top:44px">Bright Lane Promo Group, Inc. provides high-perceived value promotional incentives to businesses that want to advertise an exciting Give Away that will instantly attract more customers from your existing advertising efforts.</p>
  <p style="top:77px">Your business can give away incentive certificates that are redeemable for luxury hotel &amp; resort stays with airfare included, cruises, cash for gas, groceries, dining and even electronic goods.</p>
</section>
<div class="abs btn wide-btn" style="top:622px">Download Free Samples Of Our Incentives</div>

<h2 class="abs section-title" style="top:699px">WHY OFFER INCENTIVES TO CUSTOMERS?</h2>
<div class="abs benefit" style="left:74px"><svg width="32" height="28" viewBox="0 0 32 28"><g fill="#444"><rect x="2" y="23" width="4" height="4"/><rect x="8" y="19" width="4" height="8"/><rect x="14" y="14" width="4" height="13"/><rect x="20" y="8" width="4" height="19"/><rect x="26" y="2" width="4" height="25"/></g></svg>Increase Responses From Your Existing Ads</div>
<div class="abs benefit" style="left:202px"><svg width="32" height="28" viewBox="0 0 32 28"><path fill="#444" d="M24 2a6 6 0 0 0-5.6 8L4 24.4 6.6 27 21 12.6A6 6 0 0 0 29 7l-3.5 3.5-3-1-1-3L25 3z"/></svg>#1 Sales Closing Tool - Gift w/ Purchase</div>
<div class="abs benefit" style="left:329px"><svg width="32" height="28" viewBox="0 0 32 28"><path fill="#444" d="m16 1 4.3 8.8 9.7 1.4-7 6.8 1.7 9.6L16 23l-8.7 4.6L9 18l-7-6.8 9.7-1.4z"/></svg>Build Brand Awareness and Trust</div>
<div class="abs benefit" style="left:456px"><svg width="36" height="28" viewBox="0 0 36 28"><g fill="#444"><circle cx="8" cy="7" r="4"/><circle cx="28" cy="7" r="4"/><circle cx="18" cy="8" r="5"/><path d="M1 20c0-5 3-7 7-7s7 2 7 7zM21 20c0-5 3-7 7-7s7 2 7 7zM8 27c0-6 4-9 10-9s10 3 10 9z"/></g></svg>Insure The Sale Over Your Competition</div>
<div class="abs benefit" style="left:583px"><svg width="34" height="28" viewBox="0 0 34 28"><g fill="#444"><path d="M2 7h24V2l7 7.5-7 7.5v-5H2z"/><path d="M32 21H8v-5l-7 7.5L8 31v-5h24z" transform="translate(0,-4)"/></g></svg>Boost Repeat and Referral Business-</div>
<div class="abs benefit" style="left:710px"><svg width="34" height="28" viewBox="0 0 34 28"><rect x="1" y="4" width="32" height="20" fill="#444"/><rect x="5" y="7" width="24" height="14" fill="#f3f3f3"/><circle cx="17" cy="14" r="6" fill="#444"/><text x="17" y="18" text-anchor="middle" font-family="Roboto,sans-serif" font-size="10" font-weight="700" fill="#f3f3f3">1</text></svg>Improve Retention Rates</div>
<div class="abs btn wide-btn" style="top:870px">Download Free Samples Of Our Incentives</div>

<h2 class="abs section-title" style="top:932px">TESTIMONIALS</h2>
<div class="abs quote-badge">&#8221;</div>
<svg class="abs" style="left:110px;top:1022px" width="12" height="16" viewBox="0 0 12 16"><path d="M9 2 3 8l6 6" stroke="#777" stroke-width="1.5" fill="none"/></svg>
<svg class="abs" style="left:794px;top:1022px" width="12" height="16" viewBox="0 0 12 16"><path d="m3 2 6 6-6 6" stroke="#777" stroke-width="1.5" fill="none"/></svg>
<p class="abs quote-text">I began using your incentives two years ago to boost lead generation efforts. I have experienced a 63% increase in lead captures. And, even more importantly, my sales have increased as well. The ability to offer unlimited certificates and not having to pay for each certificate I give away is perhaps the best feature of the program, but having the flexibility to email or print certificates for my customers is also wonderful. I even use your html banners to automate my promotions right on my website!,</p>
<p class="abs quote-name">Mark T.</p>
<p class="abs quote-place">Harlow Springs, TN</p>

<footer class="abs footer">© 2017 Bright Lane Promo Group, Inc. - All Rights Reserved</footer>
<div class="abs footer-mark">M1</div>

<div class="abs overlay"></div>
<div class="abs modal" role="dialog" aria-label="Lead form">
  <div class="abs modal-photo" role="img" aria-label="Photo of two businessmen talking by a bright office window"></div>
  <div class="abs close">Close <span>X</span></div>
  <h3 class="abs form-title">ENTER YOUR INFO</h3>
  <p class="abs form-note">To be Forwarded to our website or all the<br>Details and to receive samples in your email!</p>
  <div class="abs field" style="top:86px">Name</div>
  <div class="abs field" style="top:119px">Email</div>
  <div class="abs field" style="top:153px">Phone</div>
  <div class="abs btn form-btn">Download Free Samples</div>
</div>
</body>
</html>
```